National Intensive Course Provider needs an advert designed to appear in trams

We need an advertisement designed to put in trams, the dimensions are 660mm wide and 203mm height. We offer intensive driving courses all over the UK, allowing pupils to complete a full driving course within a week/two weeks with both the theory and practical tests included in the course (as required). We would like the colours used to be green and dark blue, maybe red also, whatever looks best from them colours really.

Key Points to highlight:
- Pass your driving test within 1 week
- Start your course as early as next week
- Both tests included as part of your course (if required)

I have attached some images which could be included in the design

```html
<!DOCTYPE html>
<html lang="en">
<head>
<meta charset="utf-8">
<title>SwiftPass – Intensive Driving Courses</title>
<link href="https://fonts.googleapis.com/css2?family=Michroma&display=swap" rel="stylesheet">
<style>
  :root {
    --stage: #2b2b2d;
    --navy: #0d1140;
    --red: #e8482f;
    --red-light: #f0654a;
    --black: #070709;
    --white: #ffffff;
    --silver: #c9ccd6;
    --photo-a: #3f6b3a;
    --photo-b: #a7b8c4;
    --photo-c: #2a3550;
  }
  * { margin: 0; padding: 0; box-sizing: border-box; }
  html, body { width: 1200px; height: 630px; overflow: hidden; background: var(--stage); }
  body { font-family: "Michroma", sans-serif; color: var(--white); }

  .banner {
    position: absolute; left: 58px; top: 131px;
    width: 1083px; height: 367px; overflow: hidden;
    background: var(--red);
  }
  .banner-shapes { position: absolute; inset: 0; }

  .brand {
    position: absolute; left: 0; top: 0; width: 360px; height: 105px;
    display: flex; align-items: center; justify-content: center; gap: 12px;
  }
  .brand-dot { width: 14px; height: 14px; border-radius: 50%; background: var(--red); }
  .brand-name { font-size: 30px; letter-spacing: 1px; color: var(--white); }

  .headline {
    position: absolute; left: 502px; top: 20px; width: 560px;
    font-size: 25px; letter-spacing: -0.5px; text-align: center;
    -webkit-text-stroke: 6px var(--black); paint-order: stroke fill;
  }

  .benefits { position: absolute; left: 620px; top: 68px; list-style: none; }
  .benefit { position: relative; padding-left: 42px; margin-bottom: 19px; }
  .benefit-icon { position: absolute; left: 0; top: 2px; width: 30px; height: 22px; }
  .benefit-lead { display: block; font-size: 18.5px; line-height: 25px; }
  .benefit-rest {
    display: block; font-size: 18.5px; line-height: 25px;
    -webkit-text-stroke: 4px var(--black); paint-order: stroke fill;
  }

  .phone {
    position: absolute; left: 604px; top: 272px;
    display: flex; align-items: center; gap: 14px;
  }
  .phone-icon { width: 34px; height: 34px; }
  .phone-number { font-size: 32px; letter-spacing: 1px; }

  .website {
    position: absolute; left: 530px; top: 325px; width: 540px; height: 42px;
    display: flex; align-items: center; justify-content: center;
    font-size: 17px;
  }
</style>
</head>
<body>
  <div class="banner">
    <svg class="banner-shapes" viewBox="0 0 1083 367" width="1083" height="367">
      <defs>
        <linearGradient id="photo-tone" x1="0" y1="0" x2="1" y2="1">
          <stop offset="0" stop-color="var(--photo-c)"/>
          <stop offset="0.5" stop-color="var(--photo-b)"/>
          <stop offset="1" stop-color="var(--photo-a)"/>
        </linearGradient>
        <linearGradient id="portrait-tone" x1="0" y1="0" x2="0" y2="1">
          <stop offset="0" stop-color="#5f8a4a"/>
          <stop offset="1" stop-color="#b8333a"/>
        </linearGradient>
      </defs>
      <!-- soft diagonal light bands on the red field -->
      <polygon points="620,0 760,0 560,367 420,367" fill="var(--red-light)" opacity="0.35"/>
      <polygon points="860,0 940,0 740,367 660,367" fill="var(--red-light)" opacity="0.25"/>
      <!-- navy brand band -->
      <polygon points="0,0 372,0 430,105 0,105" fill="var(--navy)"/>
      <!-- photo area with chevron edge -->
      <polygon points="0,105 430,105 505,232 462,367 0,367" fill="url(#photo-tone)"
               role="img" aria-label="Photo of a smiling learner driver giving a thumbs up beside her instructor in a car"/>
      <!-- chevron stripes -->
      <polyline points="378,0 445,110 520,236 478,367" fill="none" stroke="var(--white)" stroke-width="10"/>
      <polyline points="398,0 462,108 538,236 497,367" fill="none" stroke="var(--navy)" stroke-width="12"/>
      <polyline points="418,0 480,106 556,236 516,367" fill="none" stroke="var(--silver)" stroke-width="4"/>
      <!-- bottom black strip -->
      <polygon points="515,325 1083,325 1083,367 490,367" fill="var(--black)"/>
      <line x1="505" y1="329" x2="525" y2="329" stroke="var(--red)" stroke-width="4"/>
      <!-- round portrait -->
      <circle cx="515" cy="207" r="80" fill="none" stroke="var(--white)" stroke-width="2" opacity="0.8"/>
      <circle cx="515" cy="207" r="70" fill="var(--white)"/>
      <circle cx="515" cy="207" r="66" fill="url(#portrait-tone)"
              role="img" aria-label="Photo of a pupil holding a pass certificate next to a red car"/>
    </svg>

    <div class="brand">
      <span class="brand-dot"></span>
      <span class="brand-name">SWIFTPASS</span>
    </div>

    <h1 class="headline">INTENSIVE DRIVING COURSES</h1>

    <ul class="benefits">
      <li class="benefit">
        <svg class="benefit-icon" viewBox="0 0 30 22"><path d="M2 11 L8 18 L16 4 M12 11 L18 18 L28 2" fill="none" stroke="#fff" stroke-width="4" stroke-linejoin="round"/></svg>
        <span class="benefit-lead">PASS YOUR DRIVING TEST</span>
        <span class="benefit-rest">WITHIN 1 WEEK</span>
      </li>
      <li class="benefit">
        <svg class="benefit-icon" viewBox="0 0 30 22"><path d="M2 11 L8 18 L16 4 M12 11 L18 18 L28 2" fill="none" stroke="#fff" stroke-width="4" stroke-linejoin="round"/></svg>
        <span class="benefit-lead">START YOUR COURSE</span>
        <span class="benefit-rest">AS EARLY AS NEXT WEEK</span>
      </li>
      <li class="benefit">
        <svg class="benefit-icon" viewBox="0 0 30 22"><path d="M2 11 L8 18 L16 4 M12 11 L18 18 L28 2" fill="none" stroke="#fff" stroke-width="4" stroke-linejoin="round"/></svg>
        <span class="benefit-lead">BOTH TESTS INCLUDED</span>
        <span class="benefit-rest">AS PART OF YOUR COURSE</span>
      </li>
    </ul>

    <div class="phone">
      <svg class="phone-icon" viewBox="0 0 24 24"><path d="M6.6 10.8a15.1 15.1 0 0 0 6.6 6.6l2.2-2.2a1 1 0 0 1 1-.25 11.4 11.4 0 0 0 3.6.57 1 1 0 0 1 1 1V20a1 1 0 0 1-1 1A17 17 0 0 1 3 4a1 1 0 0 1 1-1h3.5a1 1 0 0 1 1 1c0 1.25.2 2.45.57 3.57a1 1 0 0 1-.25 1z" fill="none" stroke="#fff" stroke-width="1.6"/><path d="M15 3a6 6 0 0 1 6 6M15 6.5a2.5 2.5 0 0 1 2.5 2.5" fill="none" stroke="#fff" stroke-width="1.6"/></svg>
      <span class="phone-number">0203 555 0192</span>
    </div>

    <div class="website">www.swiftpassdriving.com</div>
  </div>
</body>
</html>
```